Fahrzeugbeschriftung für Maschinenbaufirma
Zielgruppe
Wir sind eine Maschinenbaufirma die hauptsächlich im zerspanenden Bereich (Drehen/Fräsen/Montage) für die Branchen Automobilindustrie und Medizintechnik tätig ist.
Aufgabenstellung
Design für eine LKW-Plane
- das Design ist mit einem neuem Logo (aktuell noch nicht veröffentlicht)
- schlichtes und cleanes Design, nicht zu verspielt und zu viel Grafiken
- Abmaße LKW Plane ca. 7800mm x 2050mm (wird im Digitaldruck erstellt)
- Fahrerhaus und Boardwand sind weiß
- Beispiel Tramvel mit 'altem Logo' anbei
- es handelt sich um einen Halvorn Kestel Durmax 2240 KbT mit einem Schiebeplanen-Aufbau
- Die Plane wird im Digitaltdruck erstellt und muss nicht unbedingt weiß sein (empfindlich gegen Schmutz)
- Beispielbild wie der Schiebeplanenaufbau aussieht, anbei (nur falsche Farbe)

```html
<!DOCTYPE html>
<html lang="de">
<head>
<meta charset="utf-8">
<title>Rudolf Hallberg GmbH – Planendesign</title>
<link rel="stylesheet" href="https://fonts.googleapis.com/css2?family=Barlow:wght@400;500&display=swap">
<style>
  :root {
    --backdrop: #e9e8e6;
    --tarp: #ffffff;
    --tarp-edge: #d6d6d6;
    --brand-navy: #1f2a5a;
    --grey-text: #6e6e6e;
    --rule: #7a7a7a;
  }
  html, body {
    margin: 0;
    padding: 0;
    width: 1200px;
    height: 757px;
    overflow: hidden;
    background: var(--backdrop);
    font-family: "Barlow", Arial, sans-serif;
  }
  .tarp {
    position: absolute;
    left: 40px;
    top: 153px;
    width: 1120px;
    height: 450px;
    background: var(--tarp);
    border: 1px solid var(--tarp-edge);
    box-sizing: border-box;
  }
  .brand-mark {
    position: absolute;
    left: 500px;
    top: 85px;
    width: 119px;
    height: 119px;
    border-radius: 50%;
    background: var(--brand-navy);
  }
  .brand-name {
    position: absolute;
    left: 0;
    right: 0;
    top: 218px;
    margin: 0;
    text-align: center;
    font-weight: 500;
    font-size: 47px;
    line-height: 1;
    letter-spacing: 0.5px;
    color: var(--brand-navy);
  }
  .legal-form {
    position: absolute;
    left: 347px;
    width: 419px;
    top: 274px;
    display: flex;
    align-items: center;
    gap: 12px;
    color: var(--grey-text);
    font-size: 27px;
    font-weight: 500;
    line-height: 1;
  }
  .legal-form .rule {
    flex: 1;
    height: 2px;
    background: var(--rule);
  }
  .services {
    list-style: none;
    margin: 0;
    padding: 0;
  }
  .services li {
    position: absolute;
    top: 348px;
    font-size: 21px;
    font-weight: 500;
    color: var(--grey-text);
    letter-spacing: 0.3px;
    line-height: 1;
    white-space: nowrap;
  }
  .services .dev { left: 122px; }
  .services .prod { left: 312px; }
  .services .qa { left: 490px; }
  .services .ship { left: 758px; }
</style>
</head>
<body>
  <main class="tarp">
    <div class="brand-mark"></div>
    <h1 class="brand-name">RUDOLF HALLBERG</h1>
    <div class="legal-form"><span class="rule"></span><span>GMBH</span><span class="rule"></span></div>
    <ul class="services">
      <li class="dev">ENTWICKLUNG</li>
      <li class="prod">PRODUKTION</li>
      <li class="qa">QUALITÄTSSICHERUNG</li>
      <li class="ship">WELTWEITER VERSAND</li>
    </ul>
  </main>
</body>
</html>
```